Business Card Design Project - 2 sided

We need a business card design for a card having one business on each side (ie. two businesses on one card). Would like a design that incorporates logo, tagline and normal fields (name, position, address, phone).

Would also like an allowance for small font text along the bottom (text to be determined, but less than 50 characters).

NB. Attached logo for Harbor Quill has two variations - either can be used.

www.harborquill-example.com / www.velmaro-example.com

```html
<!DOCTYPE html>
<html lang="en">
<head>
<meta charset="utf-8">
<title>Harbor Quill / Velmaro – Business Card</title>
<link href="https://fonts.googleapis.com/css2?family=Source+Sans+3:wght@400;600;700&display=swap" rel="stylesheet">
<style>
  :root {
    --page: #ecebe8;
    --card: #ffffff;
    --green: #8cc63f;
    --green-dark: #7ab42f;
    --ink: #3f3f3f;
    --navy: #2e2f6e;
    --blue: #2f86c4;
    --rule: #8a8a8a;
    --divider: #cfcfcf;
  }
  * { box-sizing: border-box; margin: 0; padding: 0; }
  html, body { width: 1200px; height: 487px; overflow: hidden; }
  body {
    background: var(--page);
    font-family: "Source Sans 3", "Myriad Pro", sans-serif;
    color: var(--ink);
    position: relative;
  }
  .card {
    position: absolute;
    top: 89px;
    width: 542px;
    height: 310px;
    background: var(--card);
    border-radius: 14px;
    overflow: hidden;
    box-shadow: 0 1px 4px rgba(0,0,0,0.12);
  }
  .card--front { left: 41px; }
  .card--back { left: 618px; }

  .brand {
    position: absolute;
    top: 0; left: 0; right: 0;
    height: 140px;
    display: flex;
    flex-direction: column;
    align-items: center;
    justify-content: flex-end;
    padding-bottom: 16px;
  }
  .brand__row { display: flex; align-items: center; gap: 10px; }
  .brand__dot { width: 22px; height: 22px; border-radius: 50%; }
  .brand__name {
    font-weight: 600;
    line-height: 1;
    letter-spacing: 1px;
  }
  .card--front .brand__dot { background: var(--green); }
  .card--front .brand__name { color: var(--navy); font-size: 25px; text-transform: uppercase; }
  .card--back .brand__dot { background: var(--blue); }
  .card--back .brand__name { color: var(--blue); font-size: 40px; letter-spacing: 0.5px; }
  .brand__tagline {
    margin-top: 4px;
    font-size: 11px;
    color: var(--navy);
    font-weight: 600;
  }
  .card--back .brand__tagline { font-size: 13px; color: #2b4f73; letter-spacing: 0.6px; font-weight: 400; }

  .person {
    position: absolute;
    top: 160px;
    right: 288px;
    text-align: right;
  }
  .person__name { font-size: 18px; font-weight: 700; color: var(--green); }
  .person__title { font-size: 14px; font-weight: 400; color: var(--green); }
  .person__address { margin-top: 20px; font-size: 14px; line-height: 19px; }

  .divider {
    position: absolute;
    left: 269px;
    top: 158px;
    width: 1px;
    height: 86px;
    background: linear-gradient(to bottom, transparent, var(--divider) 20%, var(--divider) 80%, transparent);
  }

  .contacts {
    position: absolute;
    left: 283px;
    top: 158px;
    list-style: none;
    font-size: 14px;
    line-height: 18.2px;
  }
  .contacts li { display: flex; align-items: center; gap: 5px; }
  .contacts svg { width: 10px; height: 10px; fill: var(--green); flex: none; }

  .footer-rule {
    position: absolute;
    left: 0; right: 0;
    top: 271px;
    height: 2px;
    background: var(--rule);
  }
  .footer-band {
    position: absolute;
    left: 0; right: 0;
    top: 274px;
    bottom: 0;
    background: linear-gradient(to bottom, var(--green), var(--green-dark));
    display: flex;
    justify-content: center;
    padding-top: 3px;
    font-size: 11px;
    color: #3b4a2a;
    letter-spacing: 0.2px;
  }
</style>
</head>
<body>

<svg width="0" height="0" style="position:absolute" aria-hidden="true">
  <defs>
    <symbol id="i-phone" viewBox="0 0 10 10"><path d="M2 0.5 L3.8 2.6 L2.9 3.6 Q4 5.8 6.3 7 L7.3 6.1 L9.5 7.9 L8.4 9.5 Q3.5 9 0.5 1.8 Z"/></symbol>
    <symbol id="i-mobile" viewBox="0 0 10 10"><path d="M2.5 0 H7.5 V10 H2.5 Z M3.3 1 V7.8 H6.7 V1 Z M4.5 8.5 H5.5 V9.3 H4.5 Z"/></symbol>
    <symbol id="i-fax" viewBox="0 0 10 10"><path d="M0.5 3 H9.5 V9 H0.5 Z M2.5 0.5 H7.5 V2.5 H2.5 Z M2 5 H8 V5.8 H2 Z M2 6.8 H6 V7.6 H2 Z" fill-rule="evenodd"/></symbol>
    <symbol id="i-mail" viewBox="0 0 10 10"><path d="M0.5 3 L5 0.5 L9.5 3 V9 H0.5 Z M1.3 3.6 L5 6 L8.7 3.6 L5 1.5 Z"/></symbol>
    <symbol id="i-web" viewBox="0 0 10 10"><circle cx="5" cy="5" r="4.6"/></symbol>
  </defs>
</svg>

<section class="card card--front" aria-label="Harbor Quill side">
  <header class="brand">
    <div class="brand__row">
      <span class="brand__dot"></span>
      <span class="brand__name">Harbor Quill</span>
    </div>
    <p class="brand__tagline">Website Translation and Localisation Specialist...</p>
  </header>
  <div class="person">
    <p><span class="person__name">Your Name</span> <span class="person__title">/ Title</span></p>
    <p class="person__address">Complex name, Street<br>City, State, zip code</p>
  </div>
  <div class="divider"></div>
  <ul class="contacts">
    <li><svg><use href="#i-phone"/></svg>123-456-7890</li>
    <li><svg><use href="#i-mobile"/></svg>123-456-7890</li>
    <li><svg><use href="#i-fax"/></svg>123-456-7890</li>
    <li><svg><use href="#i-mail"/></svg>name@website.com</li>
    <li><svg><use href="#i-web"/></svg>www.website.com</li>
  </ul>
  <div class="footer-rule"></div>
  <div class="footer-band">xxxxxxxxxxxxxxxxxxxxxxxxxxxxxxxxxxxxxxxxxxxxxxxxxx</div>
</section>

<section class="card card--back" aria-label="Velmaro side">
  <header class="brand">
    <div class="brand__row">
      <span class="brand__dot"></span>
      <span class="brand__name">Velmaro LLC</span>
    </div>
    <p class="brand__tagline">Professional SEO Services</p>
  </header>
  <div class="person">
    <p><span class="person__name">Your Name</span> <span class="person__title">/ Title</span></p>
    <p class="person__address">Complex name, Street<br>City, State, zip code</p>
  </div>
  <div class="divider"></div>
  <ul class="contacts">
    <li><svg><use href="#i-phone"/></svg>123-456-7890</li>
    <li><svg><use href="#i-mobile"/></svg>123-456-7890</li>
    <li><svg><use href="#i-fax"/></svg>123-456-7890</li>
    <li><svg><use href="#i-mail"/></svg>name@website.com</li>
    <li><svg><use href="#i-web"/></svg>www.website.com</li>
  </ul>
  <div class="footer-rule"></div>
  <div class="footer-band">xxxxxxxxxxxxxxxxxxxxxxxxxxxxxxxxxxxxxxxxxxxxxxxxxx</div>
</section>

</body>
</html>
```